Business Card Design

It's an investment advisory service for individuals with all there investment needs. Also financial consulting to businesses and governmental agencies on retirement plans etc. It's personalized not commoditized help. Should show strength, knowledge and money orientation.

Reason: Will be out of town setting up office.

Reason: waiting for the 2/3rds of group to vote

Reason: only half the votes are in, I'm calling and getting verbals, but at this time we are down to 2 designs.

Industry/Entity Type

Investment

Contact Information for Business Card

B. Rel K. Financial Consulting and Wealth Management, Berislav Mike Holcek, 5172 Pasadena Loma Verde, San Diego, CA 94417-6381, Registered Investment Advisor

Requirements
Nice to have
• Something money oriented

```html
<!DOCTYPE html>
<html lang="en">
<head>
<meta charset="utf-8">
<title>B. Rel K. Financial Consulting – Business Card</title>
<link rel="stylesheet" href="https://fonts.googleapis.com/css2?family=Crimson+Text:wght@400;700&display=swap">
<style>
  :root {
    --page-bg: #1f1f1f;
    --card-white: #ffffff;
    --money-light: #eef1ea;
    --money-mid: #d9dfd2;
    --money-deep: #c6cfbd;
    --brand-green: #3d7a40;
    --band-green: #2f7a3b;
    --ink: #1d1d1b;
    --cred-green: #3f7f45;
    --text-font: "Crimson Text", Georgia, serif;
  }
  * { box-sizing: border-box; margin: 0; padding: 0; }
  html, body {
    width: 1200px;
    height: 1000px;
    overflow: hidden;
    background: var(--page-bg);
  }
  .card {
    position: absolute;
    left: 148px;
    top: 235px;
    width: 932px;
    height: 533px;
    background: var(--card-white);
    overflow: hidden;
    font-family: var(--text-font);
  }
  .money-visual {
    position: absolute;
    inset: 0 0 120px 0;
    background:
      linear-gradient(180deg, rgba(255,255,255,0) 55%, #ffffff 100%),
      linear-gradient(100deg, var(--money-deep) 0%, var(--money-light) 22%, var(--money-mid) 45%, var(--money-light) 70%, var(--money-deep) 100%);
  }
  .bottom-band {
    position: absolute;
    left: 0; right: 0; bottom: 0;
    height: 150px;
    background: linear-gradient(180deg, rgba(255,255,255,0) 0%, rgba(47,122,59,0.35) 45%, var(--band-green) 100%);
  }
  .brand-block {
    position: absolute;
    left: 0;
    top: 113px;
    width: 302px;
    height: 283px;
    background: var(--brand-green);
    color: var(--card-white);
    text-align: center;
  }
  .brand-name {
    margin-top: 52px;
    font-size: 60px;
    font-weight: 400;
    line-height: 1;
    letter-spacing: 1px;
  }
  .brand-tagline {
    margin-top: 36px;
    font-size: 19px;
    line-height: 1.15;
    letter-spacing: 0.5px;
    text-transform: uppercase;
  }
  .brand-rule {
    display: block;
    margin: 8px auto 0;
    width: 240px;
    height: 2px;
    background: var(--card-white);
  }
  .contact {
    position: absolute;
    right: 83px;
    top: 190px;
    text-align: right;
    color: var(--ink);
  }
  .person-name {
    font-size: 37px;
    font-weight: 700;
    line-height: 1.1;
  }
  .credentials {
    margin-top: 2px;
    font-size: 22px;
    color: var(--cred-green);
  }
  .credentials sup { font-size: 13px; }
  .phones {
    margin-top: 42px;
    font-size: 28px;
    line-height: 1.2;
    display: flex;
    align-items: center;
    justify-content: flex-end;
    gap: 8px;
  }
  .phone-icon { width: 24px; height: 24px; }
  .email {
    font-size: 28px;
    line-height: 1.35;
  }
  .designation {
    position: absolute;
    left: 81px;
    right: 78px;
    bottom: 30px;
    color: var(--card-white);
    font-size: 23px;
    letter-spacing: 6.6px;
    text-transform: uppercase;
    text-align: justify;
    text-align-last: justify;
    white-space: nowrap;
  }
</style>
</head>
<body>
  <div class="card">
    <div class="money-visual" role="img" aria-label="Faded photograph of fanned hundred-dollar banknotes"></div>
    <div class="bottom-band"></div>

    <div class="brand-block">
      <div class="brand-name">B. Rel K.</div>
      <div class="brand-tagline">Financial Consulting<br>&amp; Wealth Management</div>
      <span class="brand-rule"></span>
    </div>

    <div class="contact">
      <div class="person-name">Berislav “Mike” Holcek</div>
      <div class="credentials">MBA, RP<sup>©</sup>, CRC<sup>©</sup></div>
      <div class="phones">
        <svg class="phone-icon" viewBox="0 0 24 24" aria-hidden="true">
          <circle cx="12" cy="12" r="10.5" fill="none" stroke="#3f7f45" stroke-width="1.5"/>
          <path d="M8.5 6.5c-1.2.8-1.6 2.4-.8 4.3 1 2.4 3 4.8 5.2 6 1.6.9 3 .6 3.8-.4l-2.1-2.1-1.5.8c-1-.6-2.2-2-2.8-3.2l.9-1.4z" fill="#3f7f45"/>
        </svg>
        <span>858-555-0142 / 775-555-0187</span>
      </div>
      <div class="email">mike.holcek@example.com</div>
    </div>

    <div class="designation">Registered Investment Advisor</div>
  </div>
</body>
</html>
```